Website for Apartment Rental in Prague

I would like to create designs of my website focused on luxury apartment rentals in Prague, Czech Republic. I created initial mock-ups, They are all attached. I need to design homepage and subpage. The mock-ups were created by combining elements from different websites that I liked but I need you to create a design that is unique and original. The attached files a only a guidance for the structure of the website but not for the design. Try to be creative.

Apartment

```html
<!DOCTYPE html>
<html lang="en">
<head>
<meta charset="utf-8">
<title>Maison Vltava Apartments – Prague</title>
<link href="https://fonts.googleapis.com/css2?family=PT+Serif:ital,wght@0,400;0,700;1,700&family=Open+Sans:wght@400;600&family=Roboto+Condensed:wght@400;700&display=swap" rel="stylesheet">
<style>
:root{
  --orange:#e08a2e;
  --orange-dark:#c97620;
  --ink:#222222;
  --text:#555555;
  --muted:#8a8a8a;
  --light:#f2f2f2;
  --line:#dddddd;
  --footer:#6a6a6a;
  --white:#ffffff;
}
*{box-sizing:border-box;margin:0;padding:0}
html,body{width:1200px;height:3358px;overflow:hidden;background:var(--white)}
body{font-family:"Open Sans",Arial,sans-serif;color:var(--text);position:relative}
.abs{position:absolute}
.serif{font-family:"PT Serif",Georgia,serif}
.cond{font-family:"Roboto Condensed","Arial Narrow",sans-serif}

/* header */
.header{position:absolute;left:0;top:0;width:1200px;height:103px;background:var(--white)}
.hospitality{left:98px;top:5px;font-size:13px;color:var(--ink)}
.lang{display:inline-block;background:var(--orange);color:#fff;font-size:10px;padding:1px 7px;margin-left:6px}
.brand{left:98px;top:36px}
.brand-name{font-family:"PT Serif",Georgia,serif;font-weight:700;font-style:italic;color:var(--orange);font-size:27px;line-height:1}
.brand-sub{font-family:"Roboto Condensed",sans-serif;color:var(--ink);font-size:17px;margin-top:2px}
.contact{top:12px;display:flex;align-items:center;gap:14px;font-size:14px;color:var(--ink)}
.contact .ico{width:30px;height:30px;background:var(--orange);border-radius:4px;display:flex;align-items:center;justify-content:center}
.nav{left:336px;top:60px;display:flex;gap:24px;font-family:"Roboto Condensed",sans-serif;font-size:16px;color:var(--ink)}
.nav .active{color:var(--orange)}

/* hero */
.hero{left:0;top:103px;width:1200px;height:457px;background:linear-gradient(180deg,#8b7a6c 0%,#a89a8e 35%,#6e625a 70%,#4a423d 100%)}
.hero-title{left:98px;top:320px;font-family:"PT Serif",serif;font-weight:700;font-size:46px;color:#fff;text-shadow:0 2px 4px rgba(0,0,0,.4)}
.hero-sub{left:98px;top:396px;font-family:"PT Serif",serif;font-weight:700;font-size:27px;line-height:37px;color:#fff;text-shadow:0 2px 4px rgba(0,0,0,.4)}
.hero-arrow{top:496px;width:24px;height:24px;background:var(--orange);border-radius:3px}
.booking{left:808px;top:130px;width:359px;height:403px;background:rgba(15,15,15,.78);padding:28px 42px;color:#fff;font-family:"Roboto Condensed",sans-serif;font-size:15px}
.booking .field{background:#fff;color:#555;font-family:"Open Sans",sans-serif;font-size:12px;height:28px;display:flex;align-items:center;padding:0 8px;justify-content:space-between}
.row{display:flex;justify-content:space-between}
.btn{display:inline-flex;align-items:center;gap:10px;background:var(--orange);color:#fff;font-family:"PT Serif",serif;font-weight:700;font-size:14px;border-radius:4px;padding:0 6px 0 14px;height:34px}
.btn .dot{width:22px;height:22px;border-radius:50%;background:#fff;display:flex;align-items:center;justify-content:center}

/* sections */
.section-title{width:1200px;text-align:center;font-family:"PT Serif",serif;font-weight:700;font-size:34px;color:var(--ink)}
.vision-text{left:0;top:690px;width:1200px;text-align:center;font-size:13px;line-height:25px;color:var(--text)}
.feature{top:800px;width:260px;text-align:center}
.feature h3{font-family:"Roboto Condensed",sans-serif;font-weight:400;font-size:18px;color:var(--ink);margin:14px 0 10px}
.feature p{font-size:12px;line-height:23px;color:var(--muted)}

.apartments{left:0;top:1035px;width:1200px;height:595px;background:var(--light)}
.card{top:1167px;width:256px;height:311px;background:#fff;border:1px solid var(--line);padding:4px}
.card .photo{height:176px;position:relative;overflow:hidden}
.ribbon{position:absolute;right:-34px;top:20px;width:140px;transform:rotate(45deg);background:#333;color:#fff;text-align:center;font-family:"Roboto Condensed",sans-serif;font-size:13px;padding:4px 0}
.card h4{font-family:"Roboto Condensed",sans-serif;font-weight:700;font-size:17px;line-height:24px;color:var(--ink);margin:12px 8px 4px}
.meta{font-size:12px;color:var(--muted);margin:0 8px;display:flex;gap:14px}
.card .bar{display:flex;justify-content:space-between;align-items:center;margin:14px 8px 0}
.details{font-family:"PT Serif",serif;font-weight:700;color:var(--orange);font-size:14px}
.view-all{left:538px;top:1523px;width:125px;height:34px;border:2px solid var(--orange);border-radius:4px;color:var(--orange);font-family:"PT Serif",serif;font-weight:700;font-size:15px;display:flex;align-items:center;justify-content:center}

.banner{left:0;top:1630px;width:1200px;height:392px;background:linear-gradient(90deg,#b49d88 0%,#c9b7a4 50%,#a38f7c 100%)}
.banner-text{left:0;top:1712px;width:1200px;text-align:center;font-family:"PT Serif",serif;font-size:28px;line-height:42px;color:#fff}

.tour{left:0;top:2022px;width:1200px;height:520px;background:linear-gradient(180deg,#eceae6,#f4f2ef)}
.tour-photo{left:278px;top:2164px;width:645px;height:300px;background:linear-gradient(180deg,#f5f5f3 0%,#e6e4df 55%,#8c8a88 100%)}
.tour-btn{top:2273px;width:47px;height:83px;background:var(--orange);color:#fff;font-size:12px;display:flex;flex-direction:column;align-items:center;justify-content:center;gap:8px}

.info-box{left:96px;top:2616px;width:354px;height:339px;background:var(--orange);padding:40px 30px}
.info{display:flex;align-items:center;gap:22px;height:97px;color:#fff;font-size:12px;line-height:22px}
.info .circle{flex:0 0 62px;height:62px;border-radius:50%;background:#fff;display:flex;align-items:center;justify-content:center}
.testi-title{left:500px;top:2604px;font-family:"PT Serif",serif;font-weight:700;font-size:34px;color:var(--ink)}
.testi{left:500px;top:2672px;width:602px;height:283px;border:1px solid #cfcfcf;background:#fff}
.testi-photo{left:522px;top:2679px;width:177px;height:188px;background:linear-gradient(180deg,#dfe4e8,#9aa3ab)}
.testi-text{left:721px;top:2770px;width:360px;font-size:13px;line-height:23px;color:var(--text)}
.testi-quote-box{left:699px;top:2732px;width:403px;height:150px;background:#f4f4f4;border:1px solid var(--line)}
.nav-dot{top:2905px;width:24px;height:24px;border-radius:4px;background:var(--orange)}

.footer{left:0;top:3040px;width:1200px;height:318px;background:var(--footer);color:#fff}
.foot-links{font-size:13px;line-height:29px}
.social{top:3196px;width:36px;height:36px;border-radius:6px;background:var(--orange)}
.email-field{left:824px;top:3174px;width:276px;height:29px;background:#fff;display:flex;justify-content:space-between;align-items:center;padding-left:10px;font-size:11px;color:#777}
.email-field span.go{width:40px;height:29px;background:var(--orange);display:flex;align-items:center;justify-content:center}
.divider{left:96px;top:3284px;width:1008px;height:1px;background:#8a8a8a}
</style>
</head>
<body>

<header class="header">
  <div class="abs hospitality">Our Hospitality : <span class="lang">EN ▾</span></div>
  <div class="abs brand">
    <div class="brand-name">Maison Vltava</div>
    <div class="brand-sub">Apartments</div>
  </div>
  <div class="abs contact" style="left:634px">
    <span class="ico"><svg width="16" height="16" viewBox="0 0 24 24"><path fill="#fff" d="M6.6 10.8a15 15 0 0 0 6.6 6.6l2.2-2.2a1 1 0 0 1 1-.3 11.4 11.4 0 0 0 3.6.6 1 1 0 0 1 1 1V20a1 1 0 0 1-1 1A17 17 0 0 1 3 4a1 1 0 0 1 1-1h3.5a1 1 0 0 1 1 1c0 1.3.2 2.5.6 3.6a1 1 0 0 1-.3 1z"/></svg></span>
    + 420 700 123 456
  </div>
  <div class="abs contact" style="left:829px">
    <span class="ico"><svg width="16" height="14" viewBox="0 0 24 20"><rect x="1" y="2" width="22" height="16" rx="2" fill="#fff"/><path d="M2 4l10 7 10-7" stroke="#e08a2e" stroke-width="2" fill="none"/></svg></span>
    booking@vltavastay.com
  </div>
  <nav class="abs nav">
    <span class="active">Home</span><span>Apartments</span><span>Services</span><span>Location</span><span>Gallery</span><span>News</span><span>Exclusive Offers &amp; Tours</span><span>For Families</span><span>Contact Us</span>
  </nav>
</header>

<section class="abs hero" role="img" aria-label="Bright modern living room with white sofa, lounge chair and wooden wall panels"></section>
<h1 class="abs hero-title">Being Home In Prague</h1>
<p class="abs hero-sub">Sed Ut Perspiciatis Unde Omnis Iste Natus<br>Error Sit Voluptatem Accusantium Doloremque</p>
<div class="abs hero-arrow" style="left:46px"><svg width="24" height="24"><path d="M14 7l-5 5 5 5" stroke="#fff" stroke-width="2" fill="none"/></svg></div>
<div class="abs hero-arrow" style="left:80px"><svg width="24" height="24"><path d="M10 7l5 5-5 5" stroke="#fff" stroke-width="2" fill="none"/></svg></div>

<form class="abs booking">
  <div class="row"><span style="width:128px">Check In Date</span><span style="width:128px">Check Out Date</span></div>
  <div class="row" style="margin-top:6px"><div class="field" style="width:128px">dd / mm / yyyy ▦</div><div class="field" style="width:128px">dd / mm / yyyy ▦</div></div>
  <div class="row" style="margin-top:22px"><span style="width:56px">Adults</span><span style="width:56px">Children</span><span style="width:56px">Infants</span></div>
  <div class="row" style="margin-top:6px;padding-right:0"><div class="field" style="width:56px">2 ⇕</div><div class="field" style="width:56px">1 ⇕</div><div class="field" style="width:56px">1 ⇕</div></div>
  <div style="margin-top:22px">Promotional Code</div>
  <div class="field" style="margin-top:6px">Enter The Code</div>
  <div style="text-align:right;margin-top:24px"><span class="btn">Check Availability <span class="dot"><svg width="12" height="12"><path d="M2 6h8M7 3l3 3-3 3" stroke="#e08a2e" stroke-width="1.6" fill="none"/></svg></span></span></div>
  <div style="text-align:center;margin-top:8px">or</div>
  <div class="field" style="margin-top:6px">Select Rental Unit <span>▾</span></div>
</form>

<h2 class="abs section-title" style="left:0;top:628px">A Different Vision Of Travelling</h2>
<p class="abs vision-text">Something Spectacular Has Arrived In the heart of Europe. Steps from Old Town,<br>this rental experience is curated with world-class amenities, exemplary style and a feel of convenience you<br>have to experience to believe. Experience the different vision of luxury in center of Prague.</p>

<div class="abs feature" style="left:105px">
  <svg width="60" height="46" viewBox="0 0 60 46"><rect x="8" y="18" width="36" height="14" rx="3" fill="#e08a2e"/><rect x="4" y="14" width="8" height="20" rx="3" fill="#e08a2e"/><rect x="40" y="14" width="8" height="20" rx="3" fill="#e08a2e"/><rect x="8" y="34" width="3" height="5" fill="#e08a2e"/><rect x="41" y="34" width="3" height="5" fill="#e08a2e"/><path d="M52 8h6l-3 8z" fill="#e08a2e"/><rect x="54.5" y="16" width="1.5" height="22" fill="#e08a2e"/></svg>
  <h3>Passionate Room</h3>
  <p>Sed ut perspiciatis unde omnis iste natus<br>error sit voluptatem accusantium do<br>loremque laudantium</p>
</div>
<div class="abs feature" style="left:475px">
  <svg width="60" height="46" viewBox="0 0 60 46"><rect x="12" y="4" width="36" height="24" rx="2" fill="none" stroke="#e08a2e" stroke-width="3"/><circle cx="30" cy="16" r="6" fill="#e08a2e"/><rect x="18" y="32" width="24" height="4" fill="#e08a2e"/><rect x="22" y="38" width="16" height="4" fill="#e08a2e"/></svg>
  <h3>Value For Money</h3>
  <p>Sed ut perspiciatis unde omnis iste natus<br>error sit voluptatem accusantium do<br>loremque laudantium</p>
</div>
<div class="abs feature" style="left:846px">
  <svg width="60" height="46" viewBox="0 0 60 46"><circle cx="20" cy="10" r="5" fill="#e08a2e"/><path d="M6 30l14-10 10 8 22-4" stroke="#e08a2e" stroke-width="3" fill="none"/><path d="M12 26l-4 14M46 26l4 14" stroke="#e08a2e" stroke-width="3"/></svg>
  <h3>Pleasant Location</h3>
  <p>Sed ut perspiciatis unde omnis iste natus<br>error sit voluptatem accusantium do<br>loremque laudantium</p>
</div>

<section class="abs apartments"></section>
<h2 class="abs section-title" style="left:0;top:1096px">Our Apartments</h2>

<article class="abs card" style="left:148px">
  <div class="photo" role="img" aria-label="Studio apartment with round window and white furniture" style="background:linear-gradient(180deg,#cfc7bd,#8f857a)"><span class="ribbon">From 150 $</span></div>
  <h4>Brand New Luxury Living<br>Stunning Contemporary Design</h4>
  <div class="meta"><span>▬ 1 Bedroom</span><span>● 4 Members</span></div>
  <div class="bar"><span class="btn">Book Now <span class="dot"><svg width="12" height="12"><path d="M2 6h8M7 3l3 3-3 3" stroke="#e08a2e" stroke-width="1.6" fill="none"/></svg></span></span><span class="details">View Details »</span></div>
</article>
<article class="abs card" style="left:472px">
  <div class="photo" role="img" aria-label="Bright living room with sofa and pendant lamps" style="background:linear-gradient(180deg,#e4e6e6,#a8b0b2)"><span class="ribbon">From 150 $</span></div>
  <h4>Brand New Zen Luxury Living<br>Apartment In Center Of Prague</h4>
  <div class="meta"><span>▬ 1 Bedroom</span><span>● 4 Members</span></div>
  <div class="bar"><span class="btn">Book Now <span class="dot"><svg width="12" height="12"><path d="M2 6h8M7 3l3 3-3 3" stroke="#e08a2e" stroke-width="1.6" fill="none"/></svg></span></span><span class="details">View Details »</span></div>
</article>
<article class="abs card" style="left:795px">
  <div class="photo" role="img" aria-label="Open-plan apartment with wooden floor" style="background:linear-gradient(180deg,#d9d2cb,#7a5d45)"><span class="ribbon">From 150$</span></div>
  <h4>Brand New Modern Apartment<br>Unbeatable Location</h4>
  <div class="meta"><span>▬ 1 Bedroom</span><span>● 4 Members</span></div>
  <div class="bar"><span class="btn">Book Now <span class="dot"><svg width="12" height="12"><path d="M2 6h8M7 3l3 3-3 3" stroke="#e08a2e" stroke-width="1.6" fill="none"/></svg></span></span><span class="details">View Details »</span></div>
</article>
<div class="abs view-all">View All</div>

<section class="abs banner" role="img" aria-label="Softly faded kitchen interior in warm tones"></section>
<p class="abs banner-text">Maison Vltava Offers short term and as well as long term<br>options in our studio apartments and our one bedroom apartment<br>homes. Our Luxirious and high quality customer service have<br>allowed us to dominate the Prague</p>
<div class="abs" style="left:524px;top:1915px"><span class="btn">Learn More <span class="dot"><svg width="12" height="12"><path d="M2 6h8M7 3l3 3-3 3" stroke="#e08a2e" stroke-width="1.6" fill="none"/></svg></span></span></div>

<section class="abs tour"></section>
<h2 class="abs section-title" style="left:0;top:2090px">Photo Tour</h2>
<div class="abs tour-photo" role="img" aria-label="Living room with grey sofa, bicycle on wall and floor lamp"></div>
<div class="abs tour-btn" style="left:231px"><svg width="22" height="22"><circle cx="11" cy="11" r="10" fill="none" stroke="#fff" stroke-width="1.5"/><path d="M15 11H7M10 8l-3 3 3 3" stroke="#fff" stroke-width="1.5" fill="none"/></svg>Prev</div>
<div class="abs tour-btn" style="left:923px"><svg width="22" height="22"><circle cx="11" cy="11" r="10" fill="none" stroke="#fff" stroke-width="1.5"/><path d="M7 11h8M12 8l3 3-3 3" stroke="#fff" stroke-width="1.5" fill="none"/></svg>Next</div>

<aside class="abs info-box">
  <div class="info"><span class="circle"><svg width="22" height="26"><rect x="3" y="1" width="16" height="24" rx="2" fill="none" stroke="#e08a2e" stroke-width="2"/><rect x="7" y="6" width="8" height="8" fill="#e08a2e"/></svg></span>Also Available to rent all the apartments<br>together for Companies or Groups</div>
  <div class="info"><span class="circle"><svg width="26" height="26"><rect x="2" y="4" width="22" height="20" rx="2" fill="none" stroke="#e08a2e" stroke-width="2"/><path d="M2 10h22M8 1v6M18 1v6" stroke="#e08a2e" stroke-width="2"/></svg></span>Check-in : 3 pm (Flexible)<br>Check-out : 12 pm (Flexible)</div>
  <div class="info"><span class="circle"><svg width="28" height="20"><rect x="1" y="2" width="26" height="16" rx="2" fill="none" stroke="#e08a2e" stroke-width="2"/><circle cx="14" cy="10" r="4" fill="#e08a2e"/></svg></span>Starts From 150 $ per Night<br>Including Tax</div>
</aside>

<h2 class="abs testi-title">Testimonials</h2>
<div class="abs testi"></div>
<div class="abs testi-quote-box"></div>
<div class="abs testi-photo" role="img" aria-label="Portrait of guest in a dark suit"></div>
<p class="abs testi-text">Sed ut perspiciatis unde omnis iste natus error sit voluptatem accusantium doloremque laudantium, totam rem aperiam, eaque ipsa quae ab illo inventore veritatis et quasi architecto beatae vitae dicta sunt explicabo.</p>
<div class="abs cond" style="left:522px;top:2890px;width:177px;text-align:center;font-size:19px;color:var(--ink)">Marek</div>
<div class="abs" style="left:522px;top:2916px;width:177px;text-align:center;color:#d9c21c;font-size:16px;letter-spacing:1px">★★★★★</div>
<div class="abs nav-dot" style="left:1026px"><svg width="24" height="24"><path d="M14 8l-4 4 4 4" stroke="#fff" stroke-width="2" fill="none"/></svg></div>
<div class="abs nav-dot" style="left:1056px"><svg width="24" height="24"><path d="M10 8l4 4-4 4" stroke="#fff" stroke-width="2" fill="none"/></svg></div>

<footer class="abs footer"></footer>
<div class="abs" style="left:98px;top:3112px">
  <div class="brand-name">Maison Vltava</div>
  <div class="brand-sub" style="color:#fff">Apartments</div>
</div>
<div class="abs social" style="left:98px"></div>
<div class="abs social" style="left:150px"></div>
<div class="abs social" style="left:202px"></div>
<div class="abs social" style="left:253px"></div>

<div class="abs cond" style="left:408px;top:3072px;font-size:20px;color:#fff">Links</div>
<div class="abs foot-links" style="left:408px;top:3112px;color:#fff">Home<br>Apartments<br>Services<br>Location<br>Gallery</div>
<div class="abs foot-links" style="left:544px;top:3112px;color:#fff">News<br>Exclusive Offers &amp; Tours<br>For Families<br>Contact Us</div>

<div class="abs cond" style="left:824px;top:3066px;font-size:20px;color:#fff">Newsletter Subscription</div>
<p class="abs" style="left:824px;top:3114px;width:280px;font-size:12px;line-height:24px;color:#fff">Sed ut perspiciatis unde omnis iste natus error sit voluptatem accusantium doloremque</p>
<div class="abs email-field">Enter Email <span class="go"><svg width="14" height="14"><path d="M1 7l12-6-4 12-2-5z" fill="#fff"/></svg></span></div>

<div class="abs divider"></div>
<div class="abs" style="left:0;top:3308px;width:1200px;text-align:center;font-size:12px;color:#fff">Copyright © 2017, Maison Vltava. All Rights Reserved.</div>

</body>
</html>
```